Website design for luxury private hair salon

I'm looking for someone to use my Logo and build me a website for my webpage www.corsetresses.com.au (You can have a look at it as it has every detail I need included on it already), however I want a fresh new appearance and it to look and feel super stylish.

I am thinking colours in black, with silver or white, beautiful hair images like the ones you'll see on the current webpage - the price list as per what you already see.

I will include a copy of my biz card on here, so you can see the feel of the card, and design a website with a similar feel. It is matt black with a foil silver.

Modern, but classic and fresh. I will also need you to be able to publish it to my URL for me as I have no idea how to do this. I need it up and running pronto!

The website will need to be able to be read clearly on all devices incluing smart phones and ipads. The URL is currently registered and hosted by Norvel Web

Thinking a Home Page - large logo etc and write up on who and what we offer
Services/Price List page - as per the price list on my current webpage
Contact Page - with a built in contact form.

Target Market(s)

Middle aged, fashionable, stylish women and men who enjoy luxury hair care and styling in an upmarket location.

Industry/Entity Type

Hair And Beauty

Number of Pages Required

3 page

Font styles to use
Other font styles liked:
• see my images for my current logo

Colors
000000
b2b2b2
a54499

Requirements
Must have
• Style
• Fast turnaround
• Be viewable on all devices, PC, ipads, smart phones
• Designer able to upload it so its a running website for me to my URL
Nice to have
• Just a really feminine, stylish website which is easy to read and shows some beautiful images of perfect hair
Should not have
• Browns, reds or orange colours.

```html
<!DOCTYPE html>
<html lang="en">
<head>
<meta charset="utf-8">
<title>Velora hair &amp; body</title>
<link rel="stylesheet" href="https://fonts.googleapis.com/css2?family=Montserrat:wght@300;400;500;700;800&family=Raleway:wght@400;500&display=swap">
<style>
  :root {
    --black: #000000;
    --night: #0b0b0d;
    --silver: #b2b2b2;
    --plum: #a54499;
    --plum-soft: #c653bd;
    --mist: #e3e3e3;
    --ink: #2a2a2a;
    --white: #ffffff;
    --blonde: #f4e3b4;
    --blonde-deep: #d9bf86;
  }
  * { box-sizing: border-box; margin: 0; padding: 0; }
  html, body { width: 1081px; height: 1200px; overflow: hidden; background: var(--black); }
  body { position: relative; font-family: "Montserrat", sans-serif; color: var(--white); }

  .hero { position: absolute; left: 0; top: 0; width: 1081px; height: 493px; overflow: hidden;
    background:
      radial-gradient(ellipse 230px 260px at 190px 230px, rgba(250,236,200,0.95) 0%, rgba(244,227,180,0.85) 35%, rgba(217,191,134,0) 100%),
      radial-gradient(ellipse 330px 420px at 230px 240px, rgba(236,214,160,0.9) 0%, rgba(200,172,120,0.55) 55%, rgba(60,50,48,0) 100%),
      radial-gradient(ellipse 260px 120px at 300px 500px, rgba(70,66,92,0.8) 0%, rgba(40,36,50,0) 100%),
      linear-gradient(90deg, #cbb182 0%, #8c7a66 36%, #2b2427 52%, #120f11 66%, #0a090a 100%); }
  .nav { position: absolute; left: 570px; top: 24px; width: 511px; height: 42px; background: var(--plum);
    display: flex; align-items: center; justify-content: space-around; padding: 0 10px 0 6px; }
  .nav a { color: var(--white); text-decoration: none; font-size: 12.5px; font-weight: 400; }
  .brand { position: absolute; left: 470px; top: 86px; width: 560px; text-align: center; }
  .brand-name { font-size: 172px; font-weight: 300; line-height: 1; letter-spacing: 1px; }
  .brand-tag { font-size: 40px; font-weight: 400; letter-spacing: 3px; margin-top: 14px; padding-left: 80px; line-height: 1; }
  .tagline { position: absolute; right: 78px; top: 396px; text-align: center; }
  .tagline-main { font-size: 33px; font-weight: 800; color: var(--plum); line-height: 1.1; }
  .tagline-sub { font-size: 19px; font-weight: 400; color: var(--silver); letter-spacing: 1px; }

  .tile { position: absolute; top: 493px; width: 360px; overflow: hidden; }
  .tile-hair { left: 0; height: 235px;
    background:
      radial-gradient(ellipse 120px 40px at 200px 10px, rgba(150,150,150,0.7) 0%, rgba(60,60,60,0) 100%),
      radial-gradient(ellipse 90px 200px at 70px 150px, rgba(200,200,200,0.55) 0%, rgba(90,90,90,0) 100%),
      radial-gradient(ellipse 90px 200px at 300px 140px, rgba(190,190,190,0.5) 0%, rgba(90,90,90,0) 100%),
      linear-gradient(180deg, #4a4a4a 0%, #7a7a7a 50%, #3c3c3c 100%); }
  .tile-services { left: 0; top: 728px; height: 233px; background: var(--mist); padding: 54px 0 0 43px; }
  .services-title { font-size: 25px; font-weight: 800; color: var(--plum); line-height: 1.05; }
  .services-list { font-size: 17px; font-weight: 300; color: var(--ink); line-height: 1.24; }
  .services-list strong { font-weight: 700; }
  .tile-quote { left: 360px; height: 468px; background: linear-gradient(180deg, #070a14 0%, #0b1424 40%, #13243a 100%); }
  .quote { position: absolute; left: 30px; top: 43px; width: 310px; font-size: 12px; line-height: 1.22; color: var(--plum-soft); }
  .quote-by { position: absolute; left: 30px; top: 140px; font-size: 12px; color: var(--white); }
  .quote-photo { position: absolute; left: 0; top: 160px; width: 360px; height: 308px;
    background:
      radial-gradient(ellipse 110px 70px at 185px 60px, rgba(232,228,236,0.9) 0%, rgba(180,180,200,0.4) 55%, rgba(40,60,90,0) 100%),
      radial-gradient(ellipse 120px 120px at 190px 150px, rgba(60,40,40,0.9) 0%, rgba(30,30,40,0) 100%),
      radial-gradient(ellipse 150px 80px at 170px 290px, rgba(60,90,120,0.9) 0%, rgba(30,50,70,0) 100%),
      linear-gradient(90deg, #1c3350 0%, #2f4f72 30%, #13233a 70%, #050810 100%); }
  .tile-portrait { left: 720px; width: 361px; height: 468px;
    background:
      radial-gradient(ellipse 110px 220px at 200px 220px, rgba(235,235,235,0.9) 0%, rgba(190,190,190,0.5) 50%, rgba(120,120,120,0) 100%),
      radial-gradient(ellipse 120px 120px at 230px 420px, rgba(40,40,40,0.85) 0%, rgba(40,40,40,0) 100%),
      linear-gradient(90deg, #9c9c9c 0%, #c8c8c8 35%, #8a8a8a 70%, #2e2e2e 100%); }

  .footer { position: absolute; left: 0; top: 961px; width: 1081px; height: 239px; background: var(--night); }
  .footer-brand { position: absolute; left: 39px; top: 48px; width: 180px; color: var(--plum); text-align: center; }
  .footer-brand-name { font-size: 60px; font-weight: 300; line-height: 1; }
  .footer-brand-tag { font-size: 14px; letter-spacing: 2px; padding-left: 40px; margin-top: 10px; line-height: 1; }
  .footer-about { position: absolute; left: 39px; top: 157px; width: 210px; font-family: "Raleway", sans-serif; font-size: 8px; line-height: 1.3; color: var(--white); }
  .footer-col { position: absolute; top: 50px; }
  .footer-heading { font-size: 15px; font-weight: 400; color: var(--plum); margin-bottom: 17px; }
  .footer-links { list-style: none; font-family: "Raleway", sans-serif; font-size: 8.5px; }
  .footer-links li { height: 16.2px; }
  .col-services { left: 334px; }
  .col-connect { left: 584px; }
  .social { display: flex; gap: 7px; }
  .social a { width: 31px; height: 31px; border: 1.5px solid var(--white); border-radius: 50%;
    display: flex; align-items: center; justify-content: center; }
  .social svg { width: 12px; height: 12px; }
  .col-contact { left: 874px; }
  .contact-line { display: flex; align-items: flex-start; height: 16.2px; font-family: "Raleway", sans-serif; font-size: 8.5px; }
  .contact-line svg { width: 8px; height: 8px; margin: 1px 12px 0 4px; flex: none; }
  .contact-line.indent { padding-left: 24px; }
</style>
</head>
<body>
  <header class="hero" role="img" aria-label="Photograph of a woman with long wavy blonde hair">
    <nav class="nav">
      <a href="#">home</a><a href="#">price list</a><a href="#">services</a><a href="#">contact us</a>
    </nav>
    <div class="brand">
      <div class="brand-name">Velora</div>
      <div class="brand-tag">hair &amp; body</div>
    </div>
    <div class="tagline">
      <div class="tagline-main">PROFESSIONAL</div>
      <div class="tagline-sub">HAIR CARE SERVICES</div>
    </div>
  </header>

  <div class="tile tile-hair" role="img" aria-label="Black and white photograph of long flowing hair"></div>

  <section class="tile tile-services">
    <h2 class="services-title">OUR SERVICES</h2>
    <p class="services-list">Hair Cuts - Colouring -<br><strong>Highlighting - Extensions -<br>Straightening - Bridal -</strong><br>Treatments - Products &amp; Advice</p>
  </section>

  <section class="tile tile-quote">
    <div class="quote-photo" role="img" aria-label="Photograph of a woman with dark curly hair in a fur-trimmed hood"></div>
    <p class="quote">"We pride ourselves on being able to offer a private salon experience to our clients in the exclusive suburb of Ashbury, where your hair design and colouring needs will be met with years of experience and current industry training and knowledge".</p>
    <p class="quote-by">- The Velora Team -</p>
  </section>

  <div class="tile tile-portrait" role="img" aria-label="Black and white photograph of a woman with long straight blonde hair"></div>

  <footer class="footer">
    <div class="footer-brand">
      <div class="footer-brand-name">Velora</div>
      <div class="footer-brand-tag">hair &amp; body</div>
    </div>
    <p class="footer-about">We pride ourselves on being able to offer a private salon experience to our clients in the exclusive suburb of Ashbury, where your hair design and colouring needs will be met with years of experience and current industry training and knowledge</p>

    <div class="footer-col col-services">
      <h3 class="footer-heading">SERVICES</h3>
      <ul class="footer-links">
        <li>Hair Cuts</li><li>Colouring</li><li>Highlighting</li><li>Hair Extensions</li>
        <li>Straightening</li><li>Bridal</li><li>Treatments</li><li>Producs &amp; Advice</li>
      </ul>
    </div>

    <div class="footer-col col-connect">
      <h3 class="footer-heading">CONNECT</h3>
      <div class="social">
        <a href="#" aria-label="Social profile 1"><svg viewBox="0 0 12 12"><path d="M3 9L9 3M4.5 3H9v4.5" stroke="#fff" stroke-width="1.4" fill="none"/></svg></a>
        <a href="#" aria-label="Social profile 2"><svg viewBox="0 0 12 12"><path d="M3 9L9 3M4.5 3H9v4.5" stroke="#fff" stroke-width="1.4" fill="none"/></svg></a>
        <a href="#" aria-label="Social profile 3"><svg viewBox="0 0 12 12"><path d="M3 9L9 3M4.5 3H9v4.5" stroke="#fff" stroke-width="1.4" fill="none"/></svg></a>
        <a href="#" aria-label="Social profile 4"><svg viewBox="0 0 12 12"><path d="M3 9L9 3M4.5 3H9v4.5" stroke="#fff" stroke-width="1.4" fill="none"/></svg></a>
      </div>
    </div>

    <div class="footer-col col-contact">
      <h3 class="footer-heading">CONTACT US</h3>
      <div class="contact-line"><svg viewBox="0 0 10 10"><path d="M5 0a3.5 3.5 0 0 0-3.5 3.5C1.5 6 5 10 5 10s3.5-4 3.5-6.5A3.5 3.5 0 0 0 5 0zm0 5a1.4 1.4 0 1 1 0-2.8A1.4 1.4 0 0 1 5 5z" fill="#fff"/></svg>Velora hair &amp; body , 12 Lindell Lane,</div>
      <div class="contact-line indent">Ashbury WA 6011</div>
      <div class="contact-line"><svg viewBox="0 0 10 10"><path d="M2 0.5l1.8 2-1 1.2a6 6 0 0 0 3.5 3.5l1.2-1 2 1.8-1.2 1.5C4.5 9.5 0.5 5.5 0.5 1.7z" fill="#fff"/></svg>ANNA&nbsp; 0400 000 123</div>
      <div class="contact-line"><svg viewBox="0 0 10 10"><path d="M2 0.5l1.8 2-1 1.2a6 6 0 0 0 3.5 3.5l1.2-1 2 1.8-1.2 1.5C4.5 9.5 0.5 5.5 0.5 1.7z" fill="#fff"/></svg>KATE&nbsp; 0400 000 456</div>
    </div>
  </footer>
</body>
</html>
```